Business Card Design Project

Keep it simple , using logo and colors that compliment. Logo on one side with complimentary back ground color. Other side, personal info with possible complimentary design/colors

Target Market(s)

we are a non for profit that will be seeking donations . Both monetary and in kind

Industry/Entity Type

Business

Font styles to use
Sans Serif

Colors

Designer to choose colors to be used in the design.

```html
<!DOCTYPE html>
<html lang="en">
<head>
<meta charset="utf-8">
<title>Bright Path Fund – Business Card</title>
<link rel="stylesheet" href="https://fonts.googleapis.com/css2?family=Open+Sans:wght@400;700&display=swap">
<style>
  :root {
    --navy: #2b3050;
    --yellow: #f0cf00;
    --text-light: #e6e7ee;
    --text-muted: #b9bccb;
    --backdrop: #e9e9ea;
    --card-w: 520px;
    --card-h: 297px;
  }
  * { box-sizing: border-box; margin: 0; padding: 0; }
  html, body {
    width: 1200px;
    height: 675px;
    overflow: hidden;
    background: var(--backdrop);
    font-family: "Open Sans", sans-serif;
  }
  .stage {
    width: 1200px;
    height: 675px;
    display: flex;
    align-items: center;
    justify-content: center;
    gap: 40px;
  }
  .card {
    position: relative;
    width: var(--card-w);
    height: var(--card-h);
    background: var(--navy);
    overflow: hidden;
    box-shadow: 0 6px 18px rgba(0, 0, 0, 0.18);
  }

  /* Brand name lock-up */
  .brand {
    display: flex;
    align-items: center;
    gap: 12px;
    color: var(--yellow);
    font-weight: 400;
    white-space: nowrap;
  }
  .brand-ring {
    flex: none;
    border: 3px solid var(--yellow);
    border-radius: 50%;
  }

  /* Front side */
  .card-front {
    display: flex;
    align-items: center;
    justify-content: center;
  }
  .card-front .brand { font-size: 34px; }
  .card-front .brand-ring { width: 34px; height: 34px; }

  /* Back side */
  .card-back .brand {
    position: absolute;
    top: 34px;
    right: 30px;
    font-size: 20px;
    gap: 9px;
  }
  .card-back .brand-ring { width: 22px; height: 22px; border-width: 2px; }

  .accent-area {
    position: absolute;
    right: 0;
    bottom: 0;
    width: 230px;
    height: 190px;
    background: linear-gradient(160deg, var(--navy) 0%, var(--yellow) 100%);
  }

  .holder {
    position: absolute;
    left: 38px;
    top: 104px;
  }
  .holder-name {
    color: var(--yellow);
    font-weight: 700;
    font-size: 15px;
    line-height: 1.2;
  }
  .holder-role {
    color: var(--text-muted);
    font-size: 9px;
    margin-top: 2px;
  }

  .contacts {
    position: absolute;
    left: 38px;
    top: 176px;
    list-style: none;
    color: var(--text-light);
    font-size: 12.5px;
    line-height: 1;
  }
  .contacts li {
    display: flex;
    align-items: center;
    gap: 10px;
    height: 21px;
    white-space: nowrap;
  }
  .contacts .icon {
    width: 12px;
    height: 12px;
    flex: none;
    fill: var(--yellow);
  }
  .contacts .icon-outline {
    fill: none;
    stroke: var(--yellow);
    stroke-width: 1.2;
  }
  .contacts .fax-group {
    display: inline-flex;
    align-items: center;
    gap: 8px;
    margin-left: 10px;
  }
</style>
</head>
<body>
<main class="stage">

  <section class="card card-front" aria-label="Card front">
    <div class="brand">
      <span class="brand-ring"></span>
      <span class="brand-name">Bright Path Fund</span>
    </div>
  </section>

  <section class="card card-back" aria-label="Card back">
    <div class="accent-area" role="img" aria-label="Decorative yellow wave sweeping across the lower right corner"></div>

    <div class="brand">
      <span class="brand-ring"></span>
      <span class="brand-name">Bright Path Fund</span>
    </div>

    <div class="holder">
      <p class="holder-name">Your Long Name</p>
      <p class="holder-role">Owner / President</p>
    </div>

    <ul class="contacts">
      <li>
        <svg class="icon" viewBox="0 0 12 12"><path d="M6 0a4 4 0 0 0-4 4c0 3 4 8 4 8s4-5 4-8a4 4 0 0 0-4-4zm0 5.5A1.5 1.5 0 1 1 6 2.5a1.5 1.5 0 0 1 0 3z"/></svg>
        <span>Your Commercial or office address</span>
      </li>
      <li>
        <svg class="icon" viewBox="0 0 12 12"><path d="M1 4c0-2 2-3 5-3s5 1 5 3v1H8V4H4v1H1zm1 2h8l1 5H1zm4 1a1.5 1.5 0 1 0 0 3 1.5 1.5 0 0 0 0-3z"/></svg>
        <span>00.00.00.0000</span>
        <span class="fax-group">
          <svg class="icon" viewBox="0 0 12 12"><path d="M3 0h6v3H3zM1 4h10v6H9v2H3v-2H1zm3 4v3h4V8z"/></svg>
          <span>00.00.00.0000</span>
        </span>
      </li>
      <li>
        <svg class="icon" viewBox="0 0 12 12"><path d="M0 2h12v8H0zm1 1v.4l5 3.4 5-3.4V3z"/></svg>
        <span>yourname@yourwebsite.com</span>
      </li>
      <li>
        <svg class="icon icon-outline" viewBox="0 0 12 12"><circle cx="6" cy="6" r="5.2"/><ellipse cx="6" cy="6" rx="2.2" ry="5.2"/><path d="M0.8 6h10.4"/></svg>
        <span>www.yourwebsite.com</span>
      </li>
    </ul>
  </section>

</main>
</body>
</html>
```